Looking for a cool & simple business-card-design for digital agency

Hi!

We are a web agency that offers Reputation Management, Vextor & Seo Services and software development. We like cool things, we like innovative styles.

We have uploaded our logo.

Project Deadline Extended Reason: Client does not want any designs with the colorful logo. Please send us submissions ONLY with the blac and white logo. What the client would like to see:1) Back of the card: is a silver logo on a black background2) front of the card with all the data, please use white background and black logo thank you Added Friday, May 8, 2015

Industry/Entity Type

Software

```html
<!DOCTYPE html>
<html lang="en">
<head>
<meta charset="utf-8">
<title>NetPlume Business Card</title>
<link href="https://fonts.googleapis.com/css2?family=Open+Sans:wght@400;600;700&display=swap" rel="stylesheet">
<style>
  :root {
    --backdrop: #d9d9d9;
    --card: #f7f7f5;
    --card-dark: #141414;
    --silver: #c4c6c8;
    --ink: #1b1b1b;
    --muted: #3a3a3a;
    --teal: #2b9097;
    --band-black: #141414;
    --c-teal: #14a3a0;
    --c-green: #74b43c;
    --c-magenta: #e0187f;
    --c-red: #d5232b;
    --c-orange: #f3842a;
    --c-yellow: #f7d117;
  }
  * { margin: 0; padding: 0; box-sizing: border-box; }
  html, body { width: 1200px; height: 852px; overflow: hidden; }
  body {
    background: var(--backdrop);
    font-family: "Open Sans", Arial, sans-serif;
    position: relative;
  }
  .card {
    position: absolute;
    width: 560px;
    height: 320px;
    background: var(--card);
    border-radius: 10px;
    overflow: hidden;
    box-shadow: 0 6px 18px rgba(0,0,0,0.18);
  }
  .card--back { left: 90px; top: 80px; background: var(--card-dark); }
  .card--front { left: 550px; top: 450px; }

  .brand {
    position: absolute;
    display: flex;
    align-items: center;
    gap: 14px;
    color: var(--ink);
    font-weight: 700;
    letter-spacing: 1px;
    white-space: nowrap;
  }
  .brand__square {
    width: 34px; height: 34px;
    background: var(--ink);
  }
  .card--back .brand {
    left: 0; right: 0; top: 0; bottom: 0;
    justify-content: center;
    font-size: 52px;
    color: var(--silver);
  }
  .card--back .brand__square { background: var(--silver); }
  .card--front .brand { left: 40px; top: 40px; font-size: 44px; }
  .card--front .brand__square { width: 28px; height: 28px; }

  .holder {
    position: absolute;
    left: 110px; top: 170px;
    white-space: nowrap;
  }
  .holder__name { color: var(--teal); font-weight: 700; font-size: 17px; }
  .holder__role { color: var(--muted); font-size: 12px; margin-top: 2px; padding-left: 40px; }

  .contacts {
    position: absolute;
    left: 300px; top: 128px;
    list-style: none;
    font-size: 12px;
    color: var(--muted);
    line-height: 19px;
    white-space: nowrap;
  }
  .contacts li { display: flex; align-items: center; gap: 7px; }
  .contacts svg { width: 12px; height: 12px; fill: var(--muted); flex: none; }

  .stripes {
    position: absolute;
    right: 0; top: 222px;
    display: flex;
    height: 14px;
  }
  .stripes span { width: 36px; height: 14px; }
  .s1 { background: var(--c-teal); }
  .s2 { background: var(--c-green); }
  .s3 { background: var(--c-magenta); }
  .s4 { background: var(--c-red); }
  .s5 { background: var(--c-orange); }
  .s6 { background: var(--c-yellow); }

  .base-band {
    position: absolute;
    left: 0; bottom: 0;
    width: 560px; height: 84px;
  }
</style>
</head>
<body>

  <section class="card card--back" aria-label="Card back">
    <div class="brand"><span class="brand__square"></span>NetPlume</div>
  </section>

  <section class="card card--front" aria-label="Card front">
    <div class="brand"><span class="brand__square"></span>NetPlume</div>

    <div class="holder">
      <div class="holder__name">Your Long Name</div>
      <div class="holder__role">Managing Director</div>
    </div>

    <ul class="contacts">
      <li>
        <svg viewBox="0 0 12 12"><path d="M6 0a4 4 0 0 0-4 4c0 3 4 8 4 8s4-5 4-8a4 4 0 0 0-4-4zm0 5.6A1.6 1.6 0 1 1 6 2.4a1.6 1.6 0 0 1 0 3.2z"/></svg>
        Your long commercial of office address
      </li>
      <li>
        <svg viewBox="0 0 12 12"><path d="M2.4 0.6l2 2.2-1 1.4a7 7 0 0 0 4.4 4.4l1.4-1 2.2 2-1.2 1.8C5.4 11.4 0.6 6.6 0.6 1.8z"/></svg>
        000 0 0 000 00
        <svg viewBox="0 0 12 12"><path d="M3 0h6v3H3zM1 4h10v6H9v2H3v-2H1zm3 4v3h4V8z"/></svg>
        000 0 0 000 00
      </li>
      <li>
        <svg viewBox="0 0 12 12"><path d="M0 2h12v1L6 7 0 3zm0 2.4l6 4 6-4V10H0z"/></svg>
        yourname@yourwebsite.com
      </li>
      <li>
        <svg viewBox="0 0 12 12"><circle cx="6" cy="6" r="5.4" fill="none" stroke="#3a3a3a" stroke-width="1.1"/><path d="M0.6 6h10.8M6 0.6c-3 3-3 7.8 0 10.8M6 0.6c3 3 3 7.8 0 10.8" fill="none" stroke="#3a3a3a" stroke-width="1"/></svg>
        www.yourwebsite.com
      </li>
    </ul>

    <div class="stripes" aria-hidden="true">
      <span class="s1"></span><span class="s2"></span><span class="s3"></span>
      <span class="s4"></span><span class="s5"></span><span class="s6"></span>
    </div>

    <svg class="base-band" viewBox="0 0 560 84" aria-hidden="true">
      <path d="M0 84 L0 78 C140 66 300 40 345 10 L355 2 L372 16 L560 16 L560 84 Z" fill="var(--band-black)"/>
      <path d="M345 10 L355 2 L380 2 L372 16 Z" fill="var(--c-teal)"/>
    </svg>
  </section>

</body>
</html>
```